Business card design for a dynamic IT consulting company

We need a business card design for a young firm, specialized in the Telecommunications/Consulting industry. The name of the company is Quindor and Partners Business Consulting Ltd. (Short name: Quindor and Partnes)
Quindor = solve read reverse, so we aim to be uncomplicated and solution-oriented. The small pipe in our logo is also related to the word solve. So we need a new business card design, which is simple, eye catching and something non traditional (I would probably prefer a square shaped design rather than a rectangle, but open for suggestions). Attached our logo.

Target Market(s)

Usually our customers are Tier1 Telecoms providers (Q-Netra, Palorix, etc) and their executives.

Industry/Entity Type

Business

Contact Information for Business Card

Name: Bence Tolnavari
Email: b.tolnavari@quindor.hu
Web: www.quindor.hu
Mobile: +36 30 518 2769
Title: Managing Director

Optional:
Company name: Quindor and Partners Ltd.
Address: 1087 Budapest, Tolvenka str. 28/C, Hungary

Font styles to use
Other font styles liked:
• helveticaneue_medium, Prime Regular are used now.

Colors

Designer to choose colors to be used in the design.

Requirements
Must have
• I would like to have a 2 sided design.
Nice to have
• I thought if we make the logo a bit bigger (without the company name), that could go to the back with the company name below. I though, if the pipe in the logo is somehow touchable on the business card, would be nice and unique.

```html
<!DOCTYPE html>
<html lang="en">
<head>
<meta charset="utf-8">
<title>Quindor &amp; Partners – Business Card</title>
<link rel="stylesheet" href="https://fonts.googleapis.com/css2?family=Open+Sans:wght@400;700&display=swap">
<style>
  :root {
    --page-bg: #ecebe8;
    --card-white: #ffffff;
    --card-grey: #e6e6e6;
    --pattern-tone: #dcdde3;
    --ink: #1c1c1c;
    --ink-soft: #3a3a3a;
    --brand-grey: #5f5f60;
    --magenta: #b0338f;
    --cyan: #2fa3dc;
    --card-shadow: 0 10px 28px rgba(0,0,0,0.12);
  }
  * { box-sizing: border-box; margin: 0; padding: 0; }
  html, body {
    width: 1200px; height: 900px; overflow: hidden;
    background: var(--page-bg);
    font-family: "Open Sans", Arial, sans-serif;
  }
  .canvas {
    position: relative; width: 1200px; height: 900px;
  }
  .card {
    position: absolute; left: 290px;
    width: 620px; height: 355px;
    box-shadow: var(--card-shadow);
    overflow: hidden;
  }
  .card--back { top: 70px; background: var(--card-grey); }
  .card--front { top: 475px; background: var(--card-white); }

  .back-pattern {
    position: absolute; inset: 0;
    background: linear-gradient(135deg, var(--card-grey), var(--pattern-tone) 50%, var(--card-grey));
  }
  .wordmark {
    position: absolute; display: flex; align-items: center; gap: 12px;
    font-family: "Open Sans", Arial, sans-serif; font-weight: 400;
    letter-spacing: 0.5px; white-space: nowrap;
  }
  .wordmark__square { display: block; flex: none; }
  .card--back .wordmark {
    right: 40px; bottom: 92px; font-size: 46px; color: var(--ink);
  }
  .card--back .wordmark__square { width: 18px; height: 18px; background: var(--ink); }

  .contact {
    position: absolute; left: 270px; top: 34px;
    color: var(--ink-soft); font-size: 13px; line-height: 1.45;
  }
  .contact__name { font-weight: 700; font-size: 15px; color: var(--ink); }
  .contact__title { font-size: 12px; margin-bottom: 18px; }
  .contact__address { margin-bottom: 14px; }
  .contact__lines { list-style: none; }
  .contact__lines li { display: flex; align-items: center; gap: 9px; height: 21px; }
  .contact__lines svg { width: 12px; height: 12px; flex: none; }

  .card--front .wordmark {
    left: 40px; bottom: 48px; font-size: 44px; color: var(--brand-grey);
  }
  .card--front .wordmark__square { width: 18px; height: 18px; background: var(--cyan); }
</style>
</head>
<body>
<main class="canvas">
  <section class="card card--back" aria-label="Card back">
    <div class="back-pattern" role="img" aria-label="Soft scattered pastel square pattern across the card"></div>
    <div class="wordmark"><span class="wordmark__square"></span>Quindor &amp; Partners</div>
  </section>

  <section class="card card--front" aria-label="Card front">
    <div class="contact">
      <p class="contact__name">Bence Tolnavari</p>
      <p class="contact__title">Managing Director</p>
      <p class="contact__address">1087 Budapest, Tolvenka str.<br>28/C, Hungary</p>
      <ul class="contact__lines">
        <li>
          <svg viewBox="0 0 12 12" aria-hidden="true"><path d="M2.5 1 L4.5 1 L5.3 3.4 L4 4.4 Q5 6.8 7.6 8 L8.6 6.7 L11 7.5 L11 9.5 Q10.5 11 9 11 Q1 10 1 3 Q1 1.5 2.5 1 Z" fill="var(--magenta)"/></svg>
          +36 30 518 2769
        </li>
        <li>
          <svg viewBox="0 0 12 12" aria-hidden="true"><rect x="0.5" y="2.5" width="11" height="7.5" fill="var(--ink)"/><path d="M0.8 2.8 L6 7 L11.2 2.8" stroke="#fff" stroke-width="1" fill="none"/></svg>
          b.tolnavari@quindor.hu
        </li>
        <li>
          <svg viewBox="0 0 12 12" aria-hidden="true"><circle cx="6" cy="6" r="5.5" fill="var(--cyan)"/><path d="M3 4 Q5 3 6 5 Q7 7 5 8.5 M7.5 2.5 Q9 4 8.5 6" stroke="#fff" stroke-width="1" fill="none"/></svg>
          www.quindor.hu
        </li>
      </ul>
    </div>
    <div class="wordmark"><span class="wordmark__square"></span>Quindor &amp; Partners</div>
  </section>
</main>
</body>
</html>
```